Website Design for a Luxury Wedding & Events Company

We are launching a British luxury wedding & event planning consultancy business providing bespoke, elegant and first-class service to our discerning clients in the UK and abroad. We specialize in Weddings (which will have it's on page) however we also provide service for other occasion which will be included in a single page 'Events'.

We require a company website design befitting of our luxury brand. Once designed we will post another job to code the website so that it can be hosted by HostPlume.com.

The website has to set the tone for our business and type of premium service we provide. Our website design has to be BESPOKE and have a luxury and elegant look and feel about it.

PLEASE REFER TO THE IMAGES ATTACHED TO GET AN UNDERSTANDING OF THE DESIGN CONCEPT WE WANT. ALL DESIGNS SUBMITTED MUST FOLLOW THE CONCEPT SPECIFIED!!!

We appreciate that the current budget will not permit for the design of all pages referenced above, so we are happy to have designs for up to 3 pages initially; Landing page (we have attached an examples of what we want), 'Home' page (an example is also attached) and 'About' us page. When we are happy with a particular design we can add payment for remainder of the pages required.

The final website design will have the following pages:
1a) URL Landing Page (details below)
1b) Home
2) About
3) Luxury Weddings
4) Services (this can either be a separate tab or linked to 'Luxury Weddings' - however it does need to be a separate page)
subheadings are:
> Comprehensive Wedding Planning Service
> Wedding Day Coordination Service
> Consultancy Service
5) Events
6) Gallery
7) Testimonials
8) Contact

We have a concept of the website is as follows:
URL Landing Page:
Option 1: This should just be simple but makes an immediate statement.
We have attached an image of how this could potentially look. The logo featured in the photo example needs to be replaced with our logo (reference site: http://tesslovank.com/).

Option 2: Alternatively this could be an actually door in the middle of the page - Imagine the big black gloss door at Number 14 Corwell Terrace (London Prime Minister's home).

By clicking the door knocker on either options , the 'Home Page' will be opened.

Our tag line should also be tastefully integrated:
'Exclusive Events, Masterfully Produced, Distinctively Designed'

The 'HOME PAGE' - should look like a luxury boutique office or reception lounge (luxury table, luxury head chair and luxury 2 client chairs; elegant chandelier, beautiful flowers on the table, 2 flutes of champagne on the table; and filing cabinets with drawers that are labelled with different website pages, e.g. 'about us', 'services', 'gallery', etc. By clicking on the drawers the details behind that page will open up in a separate tab/page.)

Our tag line should be on the Home Page also.

The overall concept and look and feel of website is all about taking people on a journey and giving them a glimpse of the luxury service that awaits them.

Colours: We want the general look and feel of the website to be WHITE, or OFF-WHITE with soft hints of gold to match the logo (tab/page headings could be gold). The only dark page should be the URL Landing page (ref to website images attached).

The website and images need to be compatible with mobile devices, smartphones, Tabros, etc. In terms of fit to screen, resolution etc...

We require links to our Pagewall, Quillet, Snapvuely and Boardlyne Pages (links to be provided later)

This is the rough concept and looking for designers to try to elevate this vision. :-) We are open for designers to interpret this concept in their own way.

Website wording/content is all ready to go...

We have attached our logo, and some imagery to help...

Target Market(s)

Luxury Wedding & Events Market

Industry/Entity Type

Wedding Planner

Number of Pages Required

3 page

Font styles to use
Sans Serif

Colors
ffffff

Requirements
Must have
• Tag Line:
• 'Exquisite Events, Masterfully Produced, Distinctively Designed'

```html
<!DOCTYPE html>
<html lang="en">
<head>
<meta charset="utf-8">
<title>Maren Holloway — Weddings &amp; Events</title>
<link rel="stylesheet" href="https://fonts.googleapis.com/css2?family=Cinzel:wght@400;500&family=Cormorant+Garamond:ital,wght@1,500&family=Open+Sans:wght@400;600&display=swap">
<style>
:root{
  --paper:#f1f0ed;
  --paper-edge:#d9d8d4;
  --ink:#1e1e1e;
  --gold:#b5883c;
  --band:#262626;
  --band-text:#a9a9a9;
  --rule:#5a5a5a;
  --footer-text:#3a3a3a;
}
*{box-sizing:border-box;margin:0;padding:0}
html,body{width:1078px;height:1200px;overflow:hidden}
body{
  position:relative;
  background:radial-gradient(ellipse at 50% 40%,#f7f7f5 0%,var(--paper) 60%,var(--paper-edge) 100%);
  font-family:"Open Sans",Arial,sans-serif;color:var(--ink);
}
.abs{position:absolute}

/* brand */
.brand{left:40px;top:170px;width:306px;text-align:center}
.brand-name{font-family:"Open Sans",Arial,sans-serif;font-weight:400;font-size:26px;letter-spacing:3px;line-height:1;text-transform:uppercase}
.brand-note{font-family:"Open Sans",Arial,sans-serif;font-size:10px;letter-spacing:2px;margin-top:8px;text-transform:uppercase;color:var(--footer-text)}

/* navigation */
.main-nav{left:50px;top:268px;width:181px;list-style:none}
.main-nav li{font-family:"Cinzel",serif;font-size:13.5px;height:39px;border-bottom:1px solid var(--rule);padding-top:7px}
.main-nav li:first-child{height:33px;padding-top:5px}

.tagline{left:305px;top:316px;font-family:"Cormorant Garamond",serif;font-style:italic;font-weight:500;font-size:23px;line-height:34.5px;color:var(--gold)}

.hero{left:0;top:0}
.slider-dots{left:518px;top:608px;display:flex;gap:8px}
.slider-dots span{width:8px;height:8px;border-radius:50%;background:#d8c7a6}
.slider-dots span:first-child{background:var(--gold)}

/* welcome band */
.welcome{left:0;top:644px;width:1078px;height:255px;background:var(--band);text-align:center}
.welcome h1{font-family:"Cinzel",serif;font-weight:400;font-size:27px;color:var(--gold);margin-top:52px;letter-spacing:1px}
.divider{display:block;margin:12px auto 0}
.welcome p{width:800px;margin:22px auto 0;font-size:10.5px;line-height:21.6px;color:var(--band-text)}

/* footer */
.footer-col h2{font-family:"Cinzel",serif;font-weight:400;font-size:13.5px;color:var(--gold);margin-bottom:8px;letter-spacing:.5px}
.footer-col ul{list-style:none}
.footer-col li,.footer-col .note{font-size:8.5px;line-height:19.2px;text-transform:uppercase;color:var(--footer-text)}
.col-welcome{left:91px;top:936px}
.col-services{left:261px;top:936px}
.col-news{left:515px;top:936px;width:245px}
.col-follow{left:808px;top:936px;width:200px}
.email-field{margin-top:9px;width:244px;height:28px;border:1px solid #b9b9b9;background:#fff;border-radius:2px;font-size:8.5px;color:#999;padding:8px 11px;text-transform:uppercase}
.subscribe{margin-top:10px;width:114px;height:31px;border-radius:2px;background:linear-gradient(#c9a25d,#a77a34);color:#fff;font-family:"Cinzel",serif;font-size:9.5px;text-align:center;line-height:31px}
.social{list-style:none;display:grid;grid-template-columns:1fr 1fr;gap:6px 8px;margin-top:10px}
.social li{display:flex;align-items:center;gap:6px;font-family:"Cinzel",serif;font-size:10px;color:var(--gold)}
.social li::before{content:"";width:14px;height:14px;border-radius:50%;background:var(--gold)}
.mini-brand{margin-top:22px;width:130px;text-align:center}
.mini-brand .name{font-family:"Open Sans",Arial,sans-serif;font-size:10.5px;letter-spacing:1.5px;line-height:1;text-transform:uppercase}

.footer-rule{left:0;top:1146px;width:1078px;height:1px;background:#cfcfcc}
.copyright{left:0;top:1164px;width:1078px;text-align:center;font-size:8.5px;color:var(--footer-text);text-transform:uppercase}
</style>
</head>
<body>

<header class="brand abs">
  <div class="brand-name">Maren Holloway</div>
  <div class="brand-note">Weddings &amp; Events</div>
</header>

<ul class="main-nav abs">
  <li>Home</li><li>About Us</li><li>Luxury Weddings</li><li>Services</li>
  <li>Events</li><li>Gallery</li><li>Testimonials</li><li>Contact Us</li>
</ul>

<p class="tagline abs">Exclusive Events,<br>Masterfully Produced,<br>Distinctively Designed</p>

<svg class="hero abs" width="1078" height="600" viewBox="0 0 1078 600">
  <defs>
    <linearGradient id="goldFrame" x1="0" y1="0" x2="1" y2="1">
      <stop offset="0" stop-color="#f0d66a"/><stop offset=".5" stop-color="#c9a52a"/><stop offset="1" stop-color="#e8cb55"/>
    </linearGradient>
    <linearGradient id="photoGarden" x1="0" y1="0" x2="0" y2="1">
      <stop offset="0" stop-color="#8c8a84"/><stop offset=".6" stop-color="#b9b3ab"/><stop offset="1" stop-color="#5f8f3a"/>
    </linearGradient>
    <radialGradient id="photoRing"><stop offset="0" stop-color="#d9987a"/><stop offset=".55" stop-color="#8a3a2a"/><stop offset="1" stop-color="#1a0d0a"/></radialGradient>
    <radialGradient id="photoCard"><stop offset="0" stop-color="#efe6d6"/><stop offset=".6" stop-color="#b59468"/><stop offset="1" stop-color="#4a3422"/></radialGradient>
    <linearGradient id="photoCouple" x1="0" y1="0" x2="1" y2="1"><stop offset="0" stop-color="#a7664a"/><stop offset=".5" stop-color="#e8e4e6"/><stop offset="1" stop-color="#c9b8b5"/></linearGradient>
  </defs>

  <rect x="485" y="88" width="297" height="208" fill="url(#goldFrame)" stroke="#a8871c"/>
  <rect x="510" y="114" width="247" height="156" fill="none" stroke="#a8871c" stroke-width="2"/>
  <rect x="518" y="122" width="231" height="140" fill="url(#photoGarden)" role="img" aria-label="Photograph of a bride and groom celebrating with guests on a lawn"/>

  <ellipse cx="910" cy="192" rx="104" ry="126" fill="url(#goldFrame)" stroke="#a8871c"/>
  <ellipse cx="910" cy="192" rx="72" ry="94" fill="none" stroke="#a8871c" stroke-width="2"/>
  <ellipse cx="910" cy="192" rx="65" ry="87" fill="url(#photoRing)" role="img" aria-label="Photograph of hands opening a red ring box"/>

  <circle cx="634" cy="456" r="117" fill="url(#goldFrame)" stroke="#a8871c"/>
  <circle cx="634" cy="456" r="84" fill="none" stroke="#a8871c" stroke-width="2"/>
  <circle cx="634" cy="456" r="77" fill="url(#photoCard)" role="img" aria-label="Photograph of a wedding favour with a thank you tag"/>

  <rect x="808" y="358" width="206" height="207" fill="url(#goldFrame)" stroke="#a8871c"/>
  <rect x="834" y="384" width="154" height="154" fill="none" stroke="#a8871c" stroke-width="2"/>
  <rect x="842" y="391" width="139" height="139" fill="url(#photoCouple)" role="img" aria-label="Photograph of a bride and groom under a veil"/>
</svg>

<div class="slider-dots abs"><span></span><span></span><span></span></div>

<section class="welcome abs">
  <h1>Welcome to Maren Holloway</h1>
  <svg class="divider" width="116" height="10" viewBox="0 0 116 10">
    <line x1="0" y1="5" x2="40" y2="5" stroke="var(--gold)" stroke-width="2"/>
    <line x1="76" y1="5" x2="116" y2="5" stroke="var(--gold)" stroke-width="2"/>
  </svg>
  <p>Lorem Ipsum is simply dummy text of the printing and typesetting industry. Lorem Ipsum has been the industry's standard dummy text ever since the 1500s, when an unknown printer took a galley of type and scrambled it to make a type specimen book. It has survived not only five centuries, but also the leap into electronic typesetting, remaining essentially unchanged. It was popularised in the 1960s with the release</p>
</section>

<footer>
  <div class="footer-col col-welcome abs">
    <h2>WELCOME</h2>
    <ul><li>Home</li><li>About Us</li><li>Luxury Weddings</li><li>Services</li><li>Other Special Events</li><li>Gallery</li><li>Testimonials</li><li>Contact Us</li></ul>
  </div>
  <div class="footer-col col-services abs">
    <h2>SERVICES</h2>
    <ul><li>Comprehensive Wedding Planning Service</li><li>Wedding Day Coordination Service</li><li>Consultancy Service</li></ul>
  </div>
  <div class="footer-col col-news abs">
    <h2>NEWS AND EVENTS</h2>
    <p class="note">Get our recent updates through your email id</p>
    <div class="email-field">Enter your email id</div>
    <div class="subscribe">SUBSCRIBE NOW</div>
  </div>
  <div class="footer-col col-follow abs">
    <h2>FOLLOW US</h2>
    <p class="note">Connect with our socail network</p>
    <ul class="social"><li>Pagewall</li><li>Snapvuely</li><li>Boardlyne</li><li>Quillet</li></ul>
    <div class="mini-brand">
      <div class="name">Maren Holloway</div>
    </div>
  </div>
  <div class="footer-rule abs"></div>
  <p class="copyright abs">Copyright © 2015. Maren Holloway. All rights reserved.</p>
</footer>

</body>
</html>
```